Unternehmen für Ordnung und Sauberkeit am Arbeitsplatz und Produkte zur Produktionsoptimierung benötigt Visitenkarten und Briefpapier
Zielgruppe
Produkte für Ordnung und Sauberkeit am Arbeitsplatz, Organisation von Arbeitsplätzen, Produkte zur Vereinfachung von Arbeitsabläufen, Produkte zur Produktionsoptimierung unter dem Lean Gedanke, Schlagwort: "5S", nachhaltig, sauber
Aufgabenstellung
Wir sind auf der Suche nach Visitenkarten und Briefpapier für das Unternehmen yourTidor. Nachhaltig, Sauber usw.. Unser Firmenlogo finden Sie anbei.

```html
<!DOCTYPE html>
<html lang="de">
<head>
<meta charset="utf-8">
<title>yourTidor – Visitenkarten</title>
<link rel="stylesheet" href="https://fonts.googleapis.com/css2?family=Saira:wght@600;700&family=Open+Sans:wght@600&display=swap">
<style>
  :root {
    --stage: #2a2b2d;
    --card-white: #ffffff;
    --card-shade: #e4e4e4;
    --teal: #1fa89b;
    --teal-light: #8fd9d0;
    --ink: #3c3c3c;
    --wave-grey: #b9b9b9;
  }
  * { margin: 0; padding: 0; box-sizing: border-box; }
  html, body {
    width: 1163px; height: 1200px; overflow: hidden;
    background: var(--stage);
  }
  .business-card {
    position: absolute; left: 221px;
    width: 690px; height: 384px; overflow: hidden;
    background: radial-gradient(ellipse at 40% 55%, var(--card-white) 30%, var(--card-shade) 100%);
    box-shadow: 0 6px 18px rgba(0,0,0,.55);
  }
  .card-front { top: 196px; }
  .card-back { top: 665px; }

  .wave-artwork { position: absolute; inset: 0; }
  .card-front .wave-artwork {
    clip-path: polygon(360px 0, 690px 0, 690px 384px, 650px 384px);
    background: linear-gradient(110deg, var(--wave-grey) 55%, var(--teal) 78%, var(--teal-light) 100%);
    opacity: .9;
  }
  .card-back .wave-artwork {
    clip-path: polygon(0 0, 40px 0, 330px 384px, 0 384px);
    background: linear-gradient(290deg, var(--wave-grey) 55%, var(--teal) 78%, var(--teal-light) 100%);
    opacity: .9;
  }

  .brand {
    position: absolute; display: flex; align-items: center; gap: 10px;
    font-family: "Saira", sans-serif; font-weight: 700; color: var(--ink);
    letter-spacing: -0.5px; line-height: 1;
  }
  .brand-mark { background: var(--teal); display: block; }
  .card-front .brand { left: 32px; top: 90px; font-size: 34px; }
  .card-front .brand-mark { width: 34px; height: 34px; }
  .card-back .brand { left: 354px; top: 92px; font-size: 46px; }
  .card-back .brand-mark { width: 46px; height: 46px; }

  .holder-name {
    position: absolute; left: 36px; top: 206px;
    font-family: "Saira", sans-serif; font-weight: 600; font-size: 26px;
    color: var(--teal); letter-spacing: .5px; line-height: 1.2;
  }
  .postal-address {
    position: absolute; left: 36px; top: 272px; font-style: normal;
    font-family: "Saira", sans-serif; font-weight: 600; font-size: 20px;
    line-height: 29px; color: var(--ink);
  }
  .contact-list {
    position: absolute; left: 377px; top: 276px; list-style: none;
    font-family: "Open Sans", sans-serif; font-weight: 600; font-size: 14px;
    color: var(--ink);
  }
  .contact-list li { display: flex; align-items: center; gap: 13px; height: 33px; }
  .contact-list svg { width: 17px; height: 14px; fill: var(--ink); }

  .web-address {
    position: absolute; left: 486px; top: 166px;
    font-family: "Open Sans", sans-serif; font-weight: 600; font-size: 19px;
    color: var(--teal);
  }
</style>
</head>
<body>

<section class="business-card card-front" aria-label="Visitenkarte Vorderseite">
  <div class="wave-artwork" role="img" aria-label="Geschwungene Wellenbänder in Türkis, Grau und Schwarz"></div>
  <div class="brand"><span class="brand-mark"></span>yourTidor</div>
  <h1 class="holder-name">Jonas Beispiel</h1>
  <address class="postal-address">Lindenweg 8<br>D–65189 Wiesbaden</address>
  <ul class="contact-list">
    <li><svg viewBox="0 0 17 14" aria-label="Telefon"><path d="M1 4 C4 0 13 0 16 4 L14 6 L11 4.5 L11 3 C9 2.4 8 2.4 6 3 L6 4.5 L3 6Z M4 7 L13 7 L15 13 L2 13Z"/></svg>+49(0)611 – 482710</li>
    <li><svg viewBox="0 0 17 14" aria-label="Fax"><path d="M4 0 H12 V4 H4Z M1 5 H16 V11 H13 V9 H4 V11 H1Z M5 10 H12 V14 H5Z"/></svg>+49(0)611 – 4827199</li>
    <li><svg viewBox="0 0 17 14" aria-label="E-Mail"><path d="M1 2 H16 V12 H1Z"/><path d="M1.5 2.5 L8.5 8 L15.5 2.5" fill="none" stroke="#fff" stroke-width="1.3"/></svg>info@yourtidor.de</li>
  </ul>
</section>

<section class="business-card card-back" aria-label="Visitenkarte Rückseite">
  <div class="wave-artwork" role="img" aria-label="Geschwungene Wellenbänder in Türkis, Grau und Schwarz"></div>
  <div class="brand"><span class="brand-mark"></span>yourTidor</div>
  <p class="web-address">www.yourtidor.de</p>
</section>

</body>
</html>
```